Smoker Oven Manufacturer Looking for Commercial Product Catalog

We are a small, family owned/operated international smoker oven manufacturer known for our end products and customer service. Our products include residential smokers, residential pellet grills, competition barbecue smokers, commercial smokers, commercial charbroilers, grilling and smoker accessories, sauces, spices, woods and food grade pellets. We have 6 international distributors and ship products everywhere.
Up until now, we have used individual spec sheets and a customized folder to send out information to prospects and we would like to move over to a catalog design.
We would like the final design to include red and our logo. The inside of the catalog is not as important to us as the cover, but we would like something that flows well. We like using food pictures as attention grabbers but also need balance so people who see our catalog do not think we are a restaurant. The end catalog will be about 20 pages.
Attached you will find examples of our spec sheets and the order we would like products in plus some of our current smoker images. For more information, please see our website: www.brindlekiln.com.
All of the product spec, past branding and content layout can be found in dropbox: https://www.fernvault.com/sh/qp4tzwlamr83hx2/KXTE7pQwdnrjVF3k1-hgyLs9b?dl=0
Updates

Target Market(s)

Owners/Operators/Chefs in the food industry

Industry/Entity Type

Commercial

Contact Information for Business Card

similar look and feel to the catalog

Colors
ec1f27
000000

Requirements
Must have
• Brindlekiln Logo, Red in the design but does not have to be the primary color used, products photos
Nice to have
• Food pictures

```html
<!DOCTYPE html>
<html lang="en">
<head>
<meta charset="utf-8">
<title>Brindlekiln Product Catalog Cover</title>
<link rel="stylesheet" href="https://fonts.googleapis.com/css2?family=Montserrat:wght@400;700;800&display=swap">
<style>
  :root {
    --red: #ec1f27;
    --black: #000000;
    --ink: #2b2b2d;
    --grey: #545456;
    --paper: #f4f4f4;
    --stage: #e6e3df;
  }
  html, body {
    margin: 0;
    width: 1200px;
    height: 804px;
    overflow: hidden;
    background: var(--stage);
    font-family: "Montserrat", sans-serif;
  }
  .cover {
    position: absolute;
    left: 335px;
    top: 32px;
    width: 530px;
    height: 740px;
    background: var(--paper);
    box-shadow: 0 6px 24px rgba(0,0,0,0.18);
    overflow: hidden;
  }
  .cover > * { position: absolute; }
  .rule { background: var(--red); }
  .rule--h { height: 2px; }
  .rule--v { width: 2px; }
  .block--red { background: var(--red); }
  .block--black { background: var(--black); }
  .block--grey { background: var(--grey); }
  .photo { box-shadow: inset 0 0 0 1px rgba(0,0,0,0.06); }
  .photo--product {
    background:
      radial-gradient(ellipse 55% 50% at 50% 48%, #cfd0d3 0%, #dedfe1 45%, rgba(244,244,244,0) 100%),
      linear-gradient(180deg, #f7f7f7 0%, #ececec 100%);
  }
  .photo--food-roast {
    background:
      radial-gradient(ellipse 70% 60% at 45% 45%, #e09a4e 0%, #b86a2c 45%, #6e3316 80%, #2c1408 100%);
  }
  .photo--food-glazed {
    background:
      radial-gradient(ellipse 60% 50% at 50% 50%, #b3372c 0%, #7c1e16 50%, #2a1514 85%, #151212 100%);
  }
  .brand {
    left: 60px;
    top: 116px;
    display: flex;
    align-items: center;
    gap: 8px;
  }
  .brand__mark {
    width: 12px;
    height: 12px;
    background: var(--red);
  }
  .brand__name {
    font-weight: 800;
    font-size: 24px;
    color: var(--ink);
    letter-spacing: 0.3px;
  }
  .title { left: 282px; top: 560px; margin: 0; }
  .title__kicker {
    display: block;
    font-size: 13px;
    font-weight: 400;
    letter-spacing: 6px;
    color: var(--red);
  }
  .title__main {
    display: block;
    font-size: 29px;
    font-weight: 700;
    color: var(--ink);
    line-height: 1.05;
  }
  .web {
    left: 200px;
    top: 684px;
    width: 130px;
    height: 18px;
    background: var(--ink);
    border-bottom: 2px solid var(--red);
    color: #cfcfcf;
    font-size: 8px;
    letter-spacing: 1px;
    text-align: center;
    line-height: 18px;
  }
</style>
</head>
<body>
  <main class="cover">
    <div class="brand">
      <span class="brand__mark"></span>
      <span class="brand__name">Brindlekiln</span>
    </div>

    <div class="block--grey" style="left:340px;top:38px;width:46px;height:40px"></div>
    <div class="block--black" style="left:262px;top:68px;width:100px;height:98px"></div>
    <div class="block--red" style="left:366px;top:80px;width:82px;height:74px"></div>

    <div class="rule rule--v" style="left:245px;top:30px;height:400px"></div>
    <div class="rule rule--h" style="left:245px;top:172px;width:250px"></div>
    <div class="rule rule--h" style="left:60px;top:248px;width:186px"></div>
    <div class="rule rule--h" style="left:245px;top:300px;width:230px"></div>
    <div class="rule rule--h" style="left:245px;top:426px;width:270px"></div>
    <div class="rule rule--h" style="left:60px;top:510px;width:206px"></div>
    <div class="rule rule--v" style="left:265px;top:426px;height:220px"></div>
    <div class="rule rule--v" style="left:460px;top:172px;height:254px"></div>

    <div class="photo photo--product" role="img" aria-label="Stainless steel commercial smoker cabinet on casters" style="left:262px;top:182px;width:190px;height:110px"></div>
    <div class="photo photo--food-roast" role="img" aria-label="Golden roasted whole chickens on a smoker rack" style="left:72px;top:258px;width:166px;height:116px"></div>
    <div class="photo photo--product" role="img" aria-label="Rotisserie smoker oven mounted on a towable trailer" style="left:262px;top:308px;width:190px;height:110px"></div>
    <div class="photo photo--product" role="img" aria-label="Commercial rotisserie smoker oven with open door" style="left:72px;top:384px;width:166px;height:118px"></div>
    <div class="photo photo--food-glazed" role="img" aria-label="Barbecue glazed spatchcock chicken on a grill grate" style="left:274px;top:436px;width:180px;height:118px"></div>

    <div class="block--red" style="left:84px;top:522px;width:80px;height:74px"></div>
    <div class="block--black" style="left:168px;top:514px;width:96px;height:92px"></div>
    <div class="block--grey" style="left:152px;top:598px;width:46px;height:44px"></div>

    <h1 class="title">
      <span class="title__kicker">PRODUCT</span>
      <span class="title__main">CATALOG</span>
    </h1>

    <div class="web">www.brindlekiln.com</div>
  </main>
</body>
</html>
```